Boutique Store Selling Antiques and Unique Finds

I need a Web Page designed for my Store Called "Willow Lane". I would like a very classic, muted design that looks European when pulled up. I will be selling Antiques from all over the world and Unique finds that have reproduced. I will also be selling high-end purses and jewelry with unique, reasonable products for the every-day buyer as well.

Target Market(s)

25-70 year old men and women;)

Coding

Coded - Design and coding required

Number of Pages Required

1 page

Colors

Designer to choose only greyscale colors for use in the design.

Requirements
Must have
• I want it

```html
<!DOCTYPE html>
<html lang="en">
<head>
<meta charset="utf-8">
<title>Willow Lane — Antiques &amp; Unique Finds</title>
<link href="https://fonts.googleapis.com/css2?family=Lora:wght@400;700&family=Montserrat:wght@400;500&family=Arimo&display=swap" rel="stylesheet">
<style>
:root{
  --ink:#1d1d1d;
  --text:#444444;
  --muted:#666666;
  --line:#d6d6d6;
  --topbar:#e9e9e9;
  --white:#ffffff;
  --footer:#1e1c1d;
  --footer-text:#e6e6e6;
  --hero-a:#4a4036;
  --hero-b:#2a241f;
  --band-a:#d9cbb6;
  --band-b:#c9b89f;
}
*{margin:0;padding:0;box-sizing:border-box}
html,body{width:1200px;height:2799px;overflow:hidden;background:var(--white)}
body{font-family:'Lora',serif;color:var(--ink);position:relative}
.wrap{width:977px;margin:0 auto;position:relative}

.topbar{height:52px;background:var(--topbar);border-bottom:1px solid var(--line);font-size:15px;color:var(--muted)}
.topbar .wrap{display:flex;justify-content:space-between;align-items:center;height:52px}
.topbar .left span{margin-right:22px}
.topbar .right{display:flex;align-items:center;gap:22px}
.topbar svg{vertical-align:-2px}

.brand{height:113px;display:flex;align-items:flex-end;justify-content:center;padding-bottom:24px;border-bottom:1px solid var(--line)}
.brand .name{font-family:'Lora',serif;font-weight:400;font-size:30px;letter-spacing:6px;text-transform:uppercase;color:var(--ink)}
.nav{height:66px;display:flex;justify-content:center;align-items:center;gap:65px;font-size:15px;text-transform:uppercase;color:var(--ink)}

.hero{height:698px;background:radial-gradient(ellipse at 50% 55%,#7a6648 0%,var(--hero-a) 40%,var(--hero-b) 100%);position:relative;display:flex;align-items:center;justify-content:center}
.hero h1{font-weight:700;font-size:39px;line-height:53px;color:var(--white);text-align:center;text-transform:uppercase;letter-spacing:.5px}
.dots{position:absolute;bottom:12px;left:50%;transform:translateX(-50%);display:flex;gap:8px}
.dots i{width:10px;height:10px;border-radius:50%;background:var(--white)}
.dots i.on{background:#8a8a8a}

.products{padding-top:48px}
.products h2{font-weight:400;font-size:38px;text-align:center;color:#333}
.products .rule{width:42px;height:2px;background:#333;margin:16px auto 34px}
.grid{display:grid;grid-template-columns:repeat(4,230px);column-gap:19px;row-gap:52px}
.card{height:360px;background:var(--white);box-shadow:0 0 6px rgba(0,0,0,.18);padding:10px 8px;text-align:center}
.card .photo{height:185px}
.card .price{font-size:21px;margin-top:25px;color:#333}
.card .pname{font-size:17px;margin-top:8px;color:#444}
.card .btn{display:inline-block;margin-top:14px;width:136px;height:44px;line-height:42px;border:1px solid #aaa;border-radius:22px;font-size:16px;color:#333}

.feature{margin-top:61px;height:503px;background:linear-gradient(90deg,#5a4a34 0%,#a89274 30%,var(--band-a) 48%,var(--band-b) 100%);position:relative}
.feature .text{position:absolute;left:627px;top:137px;width:403px}
.feature h3{font-weight:400;font-size:38px;color:#333;margin-bottom:22px}
.feature p{font-family:'Arimo',sans-serif;font-size:14px;line-height:25.7px;color:#333;text-align:justify}

.footer{background:var(--footer);height:393px;color:var(--footer-text);font-family:'Montserrat',sans-serif;position:relative}
.footer .logo{position:absolute;left:124px;top:110px;font-family:'Lora',serif;font-size:23px;letter-spacing:4px;text-transform:uppercase;color:var(--white)}
.social{position:absolute;left:139px;top:196px;display:flex;gap:7px}
.social span{width:37px;height:37px;border:1.5px solid var(--white);border-radius:50%;display:flex;align-items:center;justify-content:center;font-size:9px}
.fcol{position:absolute;top:55px}
.fcol h4{font-weight:400;font-size:21px;color:var(--white);margin-bottom:26px}
.links{left:435px}
.links li{list-style:none;font-size:12px;font-weight:500;text-transform:uppercase;height:30px;display:flex;align-items:center;gap:10px}
.contact{left:631px}
.contact .row{display:flex;gap:14px;align-items:flex-start;font-size:14px;margin-bottom:15px;line-height:24px}
.contact .ico{width:36px;height:36px;border-radius:50%;background:#2f2d2e;display:flex;align-items:center;justify-content:center;flex:none}
.contact .row span{padding-top:6px}
.pay{left:878px;width:220px}
.pay p{font-family:'Arimo',sans-serif;font-size:13px;line-height:24px;margin-top:-6px}
.cards{display:flex;gap:4px;margin-top:14px}
.cards span{width:39px;height:27px;background:var(--white);border-radius:3px;color:#333;font-size:8px;font-family:'Montserrat',sans-serif;display:flex;align-items:center;justify-content:center}
.copy{position:absolute;left:0;right:0;bottom:22px;text-align:center;font-size:14px}
</style>
</head>
<body>
<header>
  <div class="topbar">
    <div class="wrap">
      <div class="left"><span>My Account</span><span>|</span><span>Check Out</span></div>
      <div class="right">
        <span>Sign in</span>
        <span><svg width="14" height="15" viewBox="0 0 14 15" fill="none" stroke="#666" stroke-width="1.3"><rect x="1" y="4" width="12" height="10"/><path d="M4 4V2.5a3 3 0 0 1 6 0V4"/></svg> Cart (0)</span>
        <svg width="14" height="14" viewBox="0 0 14 14" fill="none" stroke="#333" stroke-width="2"><circle cx="6" cy="6" r="4.3"/><path d="M9 9l4 4"/></svg>
      </div>
    </div>
  </div>
  <div class="wrap brand"><div class="name">Willow Lane</div></div>
  <nav class="nav">
    <span>Home</span><span>Antique &amp; Vintage</span><span>Furnishings</span><span>Clothing &amp; Shoes</span><span>Other</span><span>Sale</span>
  </nav>
</header>

<section class="hero" role="img" aria-label="Gilded star crown resting on an old leather-bound book">
  <h1>Antique and unique<br>finds from around the world</h1>
  <div class="dots"><i></i><i class="on"></i><i></i></div>
</section>

<section class="products">
  <h2>Our Products</h2>
  <div class="rule"></div>
  <div class="wrap grid">
    <div class="card"><div class="photo" role="img" aria-label="Stacked vintage suitcases on a table" style="background:linear-gradient(#6b5a40,#2c2420)"></div><div class="price">$25.99</div><div class="pname">Product Name</div><div class="btn">View Details</div></div>
    <div class="card"><div class="photo" role="img" aria-label="Wood-panelled hallway with a stone statue" style="background:linear-gradient(#5a3a26,#2e1c12)"></div><div class="price">$25.99</div><div class="pname">Product Name</div><div class="btn">View Details</div></div>
    <div class="card"><div class="photo" role="img" aria-label="Box of assorted fabric and leather pieces" style="background:linear-gradient(#8a7658,#3a3028)"></div><div class="price">$25.99</div><div class="pname">Product Name</div><div class="btn">View Details</div></div>
    <div class="card"><div class="photo" role="img" aria-label="Antique medal on a ribbon" style="background:linear-gradient(#cfc4b8,#b3a796)"></div><div class="price">$25.99</div><div class="pname">Product Name</div><div class="btn">View Details</div></div>
    <div class="card"><div class="photo" role="img" aria-label="Row of antique leather books" style="background:linear-gradient(90deg,#5a3a22,#3a2218,#1e1a18)"></div><div class="price">$25.99</div><div class="pname">Product Name</div><div class="btn">View Details</div></div>
    <div class="card"><div class="photo" role="img" aria-label="Carved stone statue in a wooden room" style="background:linear-gradient(#6a4128,#b9ad98)"></div><div class="price">$25.99</div><div class="pname">Product Name</div><div class="btn">View Details</div></div>
    <div class="card"><div class="photo" role="img" aria-label="Leafy plant in a metal urn" style="background:linear-gradient(#3f4a30,#a9a59c)"></div><div class="price">$25.99</div><div class="pname">Product Name</div><div class="btn">View Details</div></div>
    <div class="card"><div class="photo" role="img" aria-label="Fur crown on a stack of books" style="background:linear-gradient(#cdbfae,#3b3540)"></div><div class="price">$25.99</div><div class="pname">Product Name</div><div class="btn">View Details</div></div>
  </div>
</section>

<section class="feature" role="img" aria-label="Jewelled gold crown against a damask wall">
  <div class="text">
    <h3>Antiques &amp; Unique Finds</h3>
    <p>Sed ut perspiciatis unde omnis iste natus error sit voluptatem accusantium doloremque laudantium, totam rem aperiam, eaque ipsa quae ab illo inventore veritatis et quasi architecto beatae vitae dicta sunt explicabo. Nemo enim ipsam voluptatem quia voluptas sit aspernatur aut odit aut fugit, sed quia consequuntur magni dolores eos qui ratione voluptatem sequi nesciunt.</p>
  </div>
</section>

<footer class="footer">
  <div class="logo">Willow Lane</div>
  <div class="social"><span>Kite</span><span>Reed</span><span>Lark</span><span>Moss</span><span>Fern</span></div>

  <div class="fcol links">
    <h4>QUICK LINKS</h4>
    <ul>
      <li>&rarr; Home</li><li>&rarr; Antique &amp; Vintage</li><li>&rarr; Furnishings</li><li>&rarr; Clothing &amp; Shoes</li><li>&rarr; Other</li><li>&rarr; Sale</li>
    </ul>
  </div>

  <div class="fcol contact">
    <h4>CONTACT US</h4>
    <div class="row"><div class="ico"><svg width="13" height="13" viewBox="0 0 24 24" fill="#fff"><path d="M6.6 10.8a15 15 0 0 0 6.6 6.6l2.2-2.2a1 1 0 0 1 1-.25 11.4 11.4 0 0 0 3.6.57 1 1 0 0 1 1 1V20a1 1 0 0 1-1 1A17 17 0 0 1 3 4a1 1 0 0 1 1-1h3.5a1 1 0 0 1 1 1c0 1.25.2 2.45.57 3.57a1 1 0 0 1-.25 1z"/></svg></div><span>000-121-1231</span></div>
    <div class="row"><div class="ico"><svg width="14" height="11" viewBox="0 0 14 11" fill="none" stroke="#fff" stroke-width="1.3"><rect x=".7" y=".7" width="12.6" height="9.6"/><path d="M.7.7 7 6l6.3-5.3"/></svg></div><span>info@company.com</span></div>
    <div class="row"><div class="ico"><svg width="10" height="14" viewBox="0 0 10 14" fill="#fff"><path d="M5 0a5 5 0 0 0-5 5c0 4 5 9 5 9s5-5 5-9a5 5 0 0 0-5-5zm0 7a2 2 0 1 1 0-4 2 2 0 0 1 0 4z"/></svg></div><span>2172 Lorem Ipsum<br>dummy text 32308</span></div>
  </div>

  <div class="fcol pay">
    <h4>PAYMENTS</h4>
    <p>Sed ut perspiciatis unde omnis us error sit voluptatem</p>
    <div class="cards"><span>Vesta</span><span>Marlo</span><span>Amber</span><span>Dovet</span><span>Pennly</span></div>
  </div>

  <div class="copy">© Copyrights 2021-Willow Lane.All Rights Reserved.</div>
</footer>
</body>
</html>
```